Business Card for my New Brokerage

Looking to get a business card design for my new Real Estate Brokerage.
I want it with Picture, Phone Number, Email, Website, Office Address
Name and Designation. Please add logo too.

Target Market(s)

Real Estate Investors or Home Buyers

Industry/Entity Type

Real Estate

Contact Information for Business Card

Name, Email, Phone Number, website, email, office address

Colors
EB3D1F
EC4F4E
F09395
F8D3D4
FCEDEE

Requirements
Must have
• Minimalistic, Clean, Modern, Photo
Nice to have
• White and Red Colors

```html
<!DOCTYPE html>
<html lang="en">
<head>
<meta charset="utf-8">
<title>Corvane Realty Inc — Business Card</title>
<link href="https://fonts.googleapis.com/css2?family=Montserrat:wght@500;700&family=Exo+2:wght@700&family=Arimo:wght@400&display=swap" rel="stylesheet">
<style>
  :root {
    --stage: #242424;
    --brand-red: #dd0000;
    --gold: #c4964a;
    --white: #ffffff;
    --ink: #111111;
  }
  * { margin: 0; padding: 0; box-sizing: border-box; }
  html, body { width: 1075px; height: 1200px; overflow: hidden; background: var(--stage); }
  .card {
    position: absolute;
    left: 206px;
    width: 663px;
    height: 395px;
    overflow: hidden;
    box-shadow: 3px 3px 2px #000;
  }
  .card--front { top: 187px; background: var(--white); }
  .card--back { top: 637px; background: var(--brand-red); }

  .front-shapes, .portrait { position: absolute; inset: 0; width: 663px; height: 395px; }

  .brand {
    position: absolute;
    font-family: "Montserrat", sans-serif;
    font-weight: 700;
    text-align: center;
    line-height: 1;
  }
  .brand__main { display: block; }
  .brand__sub { display: block; font-weight: 500; }

  .card--front .brand { left: 35px; top: 70px; color: var(--brand-red); }
  .card--front .brand__main { font-size: 50px; letter-spacing: -0.5px; }
  .card--front .brand__sub { font-size: 18px; letter-spacing: 5px; margin-top: 6px; }

  .card--back .brand { left: 0; right: 0; top: 160px; color: var(--white); }
  .card--back .brand__main { font-size: 84px; letter-spacing: -1px; }
  .card--back .brand__sub { font-size: 29px; letter-spacing: 9px; margin-top: 12px; }

  .person { position: absolute; left: 35px; top: 196px; }
  .person__name {
    font-family: "Exo 2", sans-serif;
    font-weight: 700;
    font-size: 28px;
    color: var(--brand-red);
    line-height: 1;
  }
  .person__role {
    font-family: "Arimo", sans-serif;
    font-size: 18px;
    color: var(--ink);
    margin-top: 3px;
  }

  .contact-list {
    position: absolute;
    left: 35px;
    top: 280px;
    list-style: none;
    font-family: "Arimo", sans-serif;
    font-size: 17px;
    color: var(--white);
  }
  .contact-list li { display: flex; align-items: center; height: 24px; white-space: nowrap; }
  .contact-list svg { width: 16px; height: 16px; margin-right: 7px; flex: none; }
</style>
</head>
<body>

<section class="card card--front">
  <svg class="portrait" viewBox="0 0 663 395" role="img" aria-label="Portrait photo of the managing director in a dark suit and tie">
    <defs>
      <linearGradient id="portraitTone" x1="0" y1="0" x2="0" y2="1">
        <stop offset="0" stop-color="#ffffff"/>
        <stop offset="0.4" stop-color="#e4ddd6"/>
        <stop offset="0.65" stop-color="#7a7470"/>
        <stop offset="1" stop-color="#2c2c2c"/>
      </linearGradient>
    </defs>
    <polygon points="340,0 663,0 663,395 297,395 323,269 330,260" fill="url(#portraitTone)"/>
  </svg>

  <svg class="front-shapes" viewBox="0 0 663 395" aria-hidden="true">
    <rect x="0" y="260" width="330" height="9" fill="var(--gold)"/>
    <polygon points="0,269 323,269 297,395 0,395" fill="var(--brand-red)"/>
  </svg>

  <div class="brand">
    <span class="brand__main">CORVANE</span>
    <span class="brand__sub">REALTY INC</span>
  </div>

  <div class="person">
    <h1 class="person__name">MARCUS ELLERY</h1>
    <p class="person__role">Managing Director</p>
  </div>

  <ul class="contact-list">
    <li>
      <svg viewBox="0 0 24 24" aria-hidden="true"><path fill="#fff" d="M6.6 10.8a15.1 15.1 0 0 0 6.6 6.6l2.2-2.2a1 1 0 0 1 1-.25 11.4 11.4 0 0 0 3.6.57 1 1 0 0 1 1 1V20a1 1 0 0 1-1 1A17 17 0 0 1 3 4a1 1 0 0 1 1-1h3.5a1 1 0 0 1 1 1c0 1.25.2 2.45.57 3.57a1 1 0 0 1-.25 1z"/></svg>
      055-210 384 617
    </li>
    <li>
      <svg viewBox="0 0 24 24" aria-hidden="true"><rect x="2" y="5" width="20" height="14" fill="#fff"/><path d="M2 5l10 8 10-8" fill="none" stroke="var(--brand-red)" stroke-width="1.6"/></svg>
      hello@corvanerealty.com
    </li>
    <li>
      <svg viewBox="0 0 24 24" aria-hidden="true"><g fill="none" stroke="#fff" stroke-width="1.8"><circle cx="12" cy="12" r="9.5"/><ellipse cx="12" cy="12" rx="4.2" ry="9.5"/><path d="M2.5 12h19M4 7h16M4 17h16"/></g></svg>
      www.corvanerealty.com
    </li>
    <li>
      <svg viewBox="0 0 24 24" aria-hidden="true"><path fill="#fff" d="M12 2a7 7 0 0 0-7 7c0 5.2 7 13 7 13s7-7.8 7-13a7 7 0 0 0-7-7zm0 9.5a2.5 2.5 0 1 1 0-5 2.5 2.5 0 0 1 0 5z"/></svg>
      18 Harlow Street, Denton
    </li>
  </ul>
</section>

<section class="card card--back">
  <div class="brand">
    <span class="brand__main">CORVANE</span>
    <span class="brand__sub">REALTY INC</span>
  </div>
</section>

</body>
</html>
```